Bright Step Path Flyer, eyecatching

Hi,
To give you an idea of the business for design purposes, #BrighttStepPath is predominantly a recruitment and people development business, ran by me dedicated to training & assisting others in achieving extra income (pt or f/t) around their current commitments, people also have the opportunity to build their own business brand with my support. My brand colours are Red, White and Black, and I would like to incorporate the following text;

#BrightStepPath

Recruiting now! Start today & start earning!

Would you like an extra income, for…
A holiday?…A new car?…Lifestyle changes?
(Can you put a tick box or something similar adjacent to each)

Are you facing…
Redundancy? Birth of a new child? Hefty bills?

If so, I have the solution.

Contact Yvonne Darcott today: (can you insert the appropriate icon for each of the contact details)
Tel: 07419 604172
Twitter: @Bright_StepPath
Email: Yvonne@brightsteppath-example.co.uk
Facebook: www.socialpage-example.com/yvonbrightsteppath

Target Market(s)

Women aged 25-45 years, possibly busy mums too, wanting to earn additinal income to allow them more choices, be it family time, money, new challenge, meeting new people, personal development

Industry/Entity Type

Health And Wellness

Font styles to use
Serif
Sans Serif
Decorative
Script

Colors
ec1f27
ffffff
000000

Requirements
Must have
• My heels logo, be clear concise and eye catching, I also have the following strap line if you wish to use;
• Empowering other to achieve
• Also I have attached a closeup picture of myself but would ideally only like half my face to appear (leftside) similar to the other picture posted - if you can
Nice to have
• Perhaps adding other forms of graphics, or the 3rd picture I have attached with myself...possibly just the shoes though
Should not have
• Too many colours

```html
<!DOCTYPE html>
<html lang="en">
<head>
<meta charset="utf-8">
<title>Bright Step Path – Recruiting Flyer</title>
<link rel="stylesheet" href="https://fonts.googleapis.com/css2?family=Crimson+Pro:wght@600;700&display=swap">
<style>
  :root {
    --red: #c1202a;
    --red-bright: #ec1f27;
    --charcoal: #2b2b2d;
    --ink: #1b1b1c;
    --white: #ffffff;
    --grey: #b4b4b4;
    --stage: #8c8c8c;
    --serif: "Crimson Pro", Georgia, serif;
  }
  * { box-sizing: border-box; margin: 0; padding: 0; }
  html, body { width: 1200px; height: 920px; overflow: hidden; }
  body { background: var(--stage); position: relative; font-family: var(--serif); }

  .flyer {
    position: absolute; left: 334px; top: 84px;
    width: 532px; height: 752px;
    background: var(--charcoal);
    overflow: hidden;
    box-shadow: 0 6px 18px rgba(0,0,0,.35);
  }
  .flyer-shapes { position: absolute; inset: 0; }

  .brand { position: absolute; left: 0; right: 0; top: 22px; text-align: center; color: var(--red); font-weight: 700; line-height: .9; }
  .brand-top { font-size: 40px; letter-spacing: 3px; }
  .brand-main { font-size: 86px; letter-spacing: 2px; }

  .tagline { position: absolute; left: 0; right: 0; top: 148px; text-align: center; color: var(--grey); font-weight: 700; font-size: 16px; line-height: 20px; letter-spacing: .3px; text-transform: uppercase; }

  .section-title { position: absolute; left: 27px; color: var(--red); font-weight: 700; font-size: 21px; line-height: 23px; text-transform: uppercase; }
  .income-title { top: 244px; }
  .facing-title { top: 408px; }

  .reason-list { position: absolute; left: 27px; list-style: none; }
  .income-list { top: 297px; }
  .facing-list { top: 430px; }
  .reason {
    display: flex; align-items: center; gap: 6px;
    height: 33px; color: var(--white); font-weight: 700; font-size: 11.5px;
    text-transform: uppercase; letter-spacing: .3px;
  }
  .reason svg { width: 24px; height: 24px; }

  .divider { position: absolute; left: 27px; top: 536px; width: 246px; height: 1px; background: var(--grey); }

  .solution { position: absolute; left: 24px; top: 554px; color: var(--white); font-weight: 700; font-size: 23px; line-height: 24px; text-transform: uppercase; }

  .logo-area { position: absolute; left: 338px; top: 196px; width: 136px; height: 136px; border-radius: 50%; background: var(--white); border: 2px solid var(--red); }
  .portrait-area {
    position: absolute; left: 306px; top: 506px; width: 204px; height: 204px; border-radius: 50%;
    border: 3px solid var(--red);
    background: radial-gradient(circle at 40% 40%, #e9d6d8 0%, #d3a9b3 55%, #b97f8e 100%);
  }

  .contact { position: absolute; left: 24px; top: 644px; color: var(--white); font-style: normal; }
  .contact-title { color: var(--ink); font-weight: 700; font-size: 19px; line-height: 18px; text-transform: uppercase; }
  .contact-name { color: var(--ink); font-weight: 700; font-size: 12px; line-height: 14px; }
  .contact-line { display: flex; align-items: center; gap: 4px; font-weight: 700; font-size: 10.5px; line-height: 17px; white-space: nowrap; }
  .contact-line.phone { font-size: 17px; line-height: 22px; letter-spacing: .5px; }
  .contact-line svg { width: 11px; height: 11px; flex: none; }
  .contact-row { display: flex; gap: 12px; }
</style>
</head>
<body>
<main class="flyer">
  <svg class="flyer-shapes" viewBox="0 0 532 752" aria-hidden="true">
    <path d="M0 214 C120 170 220 230 320 236 C400 240 470 200 532 158 L532 170 C470 214 400 256 320 252 C220 248 120 192 0 226 Z" fill="var(--red)"/>
    <path d="M0 232 C130 196 230 252 330 258 C420 262 480 225 532 190" fill="none" stroke="var(--white)" stroke-width=".8" opacity=".7"/>
    <path d="M0 648 C80 624 170 640 260 664 C330 684 360 600 420 530 C460 490 500 480 532 472 L532 752 L0 752 Z" fill="var(--red)"/>
    <path d="M400 478 C460 440 520 448 540 470" fill="none" stroke="var(--white)" stroke-width="1"/>
    <path d="M532 520 C490 470 410 470 370 510" fill="none" stroke="var(--white)" stroke-width="1"/>
    <circle cx="386" cy="620" r="118" fill="none" stroke="var(--ink)" stroke-width="1"/>
  </svg>

  <header class="brand">
    <div class="brand-top">BRIGHT STEP</div>
    <div class="brand-main">PATH</div>
  </header>
  <p class="tagline">Recruiting now!<br>Start today &amp; start earning!</p>

  <div class="logo-area" role="img" aria-label="Bright Step Path heels logo"></div>

  <h2 class="section-title income-title">Would you like<br>an extra income, for...</h2>
  <ul class="reason-list income-list">
    <li class="reason">A holiday?
      <svg viewBox="0 0 24 24"><circle cx="12" cy="12" r="10.5" fill="none" stroke="var(--red)" stroke-width="1.3"/><circle cx="12" cy="7" r="1.6" fill="var(--white)"/><path d="M12 9v6l-2 4M12 15l2 4M12 11l-3 2M12 11l3 2M16 12v6" stroke="var(--white)" stroke-width="1.3" fill="none"/></svg>
    </li>
    <li class="reason">A new car?
      <svg viewBox="0 0 24 24"><circle cx="12" cy="12" r="10.5" fill="none" stroke="var(--red)" stroke-width="1.3"/><path d="M6 14h12v-2l-2-3H8l-2 3z" fill="none" stroke="var(--white)" stroke-width="1.3"/><circle cx="8.5" cy="15" r="1.3" fill="var(--white)"/><circle cx="15.5" cy="15" r="1.3" fill="var(--white)"/></svg>
    </li>
    <li class="reason">Lifestyle changes?
      <svg viewBox="0 0 24 24"><circle cx="12" cy="12" r="10.5" fill="none" stroke="var(--red)" stroke-width="1.3"/><path d="M12 6v3M12 15v3M6 12h3M15 12h3M8 8l2 2M14 14l2 2M16 8l-2 2M10 14l-2 2" stroke="var(--white)" stroke-width="1.3"/></svg>
    </li>
  </ul>

  <h2 class="section-title facing-title">Are you facing...</h2>
  <ul class="reason-list facing-list">
    <li class="reason">Redundancy?
      <svg viewBox="0 0 24 24"><circle cx="12" cy="12" r="10.5" fill="none" stroke="var(--red)" stroke-width="1.3"/><circle cx="8" cy="9" r="1.8" fill="none" stroke="var(--white)" stroke-width="1.2"/><circle cx="8" cy="15" r="1.8" fill="none" stroke="var(--white)" stroke-width="1.2"/><path d="M9.5 10l8 5M9.5 14l8-5" stroke="var(--white)" stroke-width="1.2"/></svg>
    </li>
    <li class="reason">Birth of a new child?
      <svg viewBox="0 0 24 24"><circle cx="12" cy="12" r="10.5" fill="none" stroke="var(--red)" stroke-width="1.3"/><circle cx="12" cy="12" r="5" fill="none" stroke="var(--white)" stroke-width="1.3"/><circle cx="10.3" cy="11.3" r=".8" fill="var(--white)"/><circle cx="13.7" cy="11.3" r=".8" fill="var(--white)"/></svg>
    </li>
    <li class="reason">Hefty bills?
      <svg viewBox="0 0 24 24"><circle cx="12" cy="12" r="10.5" fill="none" stroke="var(--red)" stroke-width="1.3"/><path d="M8 10h8l1 7H7z" fill="none" stroke="var(--white)" stroke-width="1.3"/><path d="M10 10l1-3h2l1 3" fill="none" stroke="var(--white)" stroke-width="1.2"/></svg>
    </li>
  </ul>

  <div class="divider"></div>
  <p class="solution">If so, I have<br>the solution.</p>

  <div class="portrait-area" role="img" aria-label="Close-up portrait photograph of Yvonne Darcott"></div>

  <address class="contact">
    <div class="contact-title">Contact</div>
    <div class="contact-name">Yvonne Darcott today:</div>
    <div class="contact-line phone">
      <svg viewBox="0 0 12 12"><rect x="3" y="1" width="6" height="10" rx="1" fill="none" stroke="var(--white)" stroke-width="1.2"/><rect x="5" y="9" width="2" height="1" fill="var(--white)"/></svg>: 07419 604172
    </div>
    <div class="contact-line">
      <svg viewBox="0 0 12 12"><circle cx="6" cy="6" r="4.5" fill="var(--white)"/></svg>: @Bright_StepPath
    </div>
    <div class="contact-row">
      <div class="contact-line">
        <svg viewBox="0 0 12 12"><rect x="1" y="2.5" width="10" height="7" fill="none" stroke="var(--white)" stroke-width="1.1"/><path d="M1 2.5l5 4 5-4" fill="none" stroke="var(--white)" stroke-width="1.1"/></svg>: Yvonne@brightsteppath-example.co.uk
      </div>
      <div class="contact-line">
        <svg viewBox="0 0 12 12"><circle cx="6" cy="6" r="4.5" fill="var(--white)"/></svg>: www.socialpage-example.com/yvonbrightsteppath
      </div>
    </div>
  </address>
</main>
</body>
</html>
```